label design for a new car battery

Hello,
We are new startup company called VANTERCELL, we sell Lithium-Ion-Phosphate Batteries to the Motorhome, Caravan, off-grid solar power, Boats, Yachts and Marine sectors.
We are looking for a proactive and professional designer to help us create a new brand and logo for a label design to go on a battery product. It has a label on the top and on the front face (see attached images) We have some basic regulatory text and basic icons we need to incorporate but the rest of the label is available to build a brand and color scheme that will be used throughout our new website. (files attached showing our competition) We also want to incorporate a QR code for a direct link to our website on the top label
Batteries are big black boxes and very dull and boring to look at, generally with a white label stuck on the front and top. We like designs that will be on a black background so the label feels like it is printed onto the surface rather than a label stuck on to the battery.
In terms of design and layout we need to break for the norm and break with tradition to create some inspiration to make this product stand out of the label and look enticing to purchase with its modern look and vibrant color scheme.
This logo and color scheme will be used to launch our new google banner ad campaign so it has to grab potential buyers attention.

Company name: VanterCell
Product Name: Corvane +
Product Description 110AH LiFEPO4 12.8V Battery

Our competition please review ~
www.stadmerek.de
www.quorvelpack.co.uk/products.php
www.bandokrast.de

Please use our competition information as how NOT to DESIGN a logo or label.

If you feel you can help and ad some value and some cool designs please enter

Target Market(s)

Motorhomes, caravans, boats, marine sectors and off grid solar.

Logo Text

Company Name: VANTERCELL Product Name: Corvane + Website: Vantercell.co.uk

Requirements
Must have
• We are a modern company and want this reflected in our branding. We like negative space logos, freestyle line art and modern concepts. we have attached some logos we like. stylish, elegant and unique designs will win the day. simplistic is always the best. Please provide a selection of you best work rather than one basic logo.The logo and theme should consider this is an renewable energy product.
It could feature the periodic code for lithium in the lettering or the logo but this is not essential. This is just one idea. our battery is robust, durable and long lasting maybe the logo theme could incorporate this concept.

we have attached a few images of negative space icons we like.
Please see our image for the proposed layout for presentation
The label size for top logo is 230mm x 65mm
the label size for the front label is 230mm x 95mm
QR code on top label
Nice to have
• I have attached an image of how I would like the presentations to be formatted.
Negative space logo design would be excellent.
Should not have
• dated poor design, no script type fonts.
please do not waste your time submitting just text logos. we are using this on our website as a theme throughout and we a using Pitch hive for inspiration not just font variations.

This is a logo competition not a font showcase. Any submissions without a logo will be eliminated with a low rating.
Please NO old fashioned lighting bolts or battery symbols we are looking to step into. 21st century design. No repeat old designs.

Thanks

```html
<!DOCTYPE html>
<html lang="en">
<head>
<meta charset="utf-8">
<title>VanterCell – Corvane + Front Label</title>
<link href="https://fonts.googleapis.com/css2?family=Michroma&display=swap" rel="stylesheet">
<style>
  :root {
    --page: #ffffff;
    --label-black: #000000;
    --lime: #d9e021;
    --olive: #a6ae4a;
    --grey-line: #8a8f6a;
    --white: #ffffff;
  }
  * { margin: 0; padding: 0; box-sizing: border-box; }
  html, body {
    width: 1200px;
    height: 1000px;
    overflow: hidden;
    background: var(--page);
  }
  .canvas {
    position: relative;
    width: 1200px;
    height: 1000px;
  }
  .front-label {
    position: absolute;
    left: 220px;
    top: 214px;
    width: 738px;
    height: 305px;
    background: var(--label-black);
    overflow: hidden;
  }
  .label-art {
    position: absolute;
    inset: 0;
    width: 738px;
    height: 305px;
  }
  .product-name {
    position: absolute;
    left: 44px;
    top: 88px;
    font-family: "Michroma", sans-serif;
    font-size: 17px;
    letter-spacing: 2px;
    color: var(--white);
    white-space: nowrap;
  }
  .brand-name {
    position: absolute;
    left: 212px;
    top: 154px;
    font-family: "Michroma", sans-serif;
    font-size: 28px;
    letter-spacing: 4px;
    color: var(--white);
    white-space: nowrap;
  }
  .spec-text {
    position: absolute;
    left: 533px;
    top: 252px;
    font-family: "Michroma", sans-serif;
    font-size: 14px;
    line-height: 21px;
    letter-spacing: 2.5px;
    color: var(--white);
    font-variant: small-caps;
    white-space: nowrap;
  }
</style>
</head>
<body>
<div class="canvas">
  <section class="front-label">
    <svg class="label-art" viewBox="0 0 738 305" xmlns="http://www.w3.org/2000/svg">
      <defs>
        <linearGradient id="swooshFill" x1="0" y1="1" x2="1" y2="0">
          <stop offset="0" stop-color="#d9e021"/>
          <stop offset="0.35" stop-color="#8d9a55"/>
          <stop offset="0.7" stop-color="#6e6e6e"/>
          <stop offset="1" stop-color="#111111"/>
        </linearGradient>
        <radialGradient id="globeFill" cx="0.5" cy="0.5" r="0.5">
          <stop offset="0" stop-color="#9cc23a" stop-opacity="0.45"/>
          <stop offset="1" stop-color="#d9e021" stop-opacity="0.08"/>
        </radialGradient>
        <linearGradient id="networkFill" x1="0" y1="0" x2="0" y2="1">
          <stop offset="0" stop-color="#a6ae4a" stop-opacity="0.12"/>
          <stop offset="1" stop-color="#d9e021" stop-opacity="0.3"/>
        </linearGradient>
      </defs>

      <!-- plain guide lines, left -->
      <g class="guide-lines" fill="none" stroke-width="2">
        <line x1="114" y1="0" x2="114" y2="62" stroke="var(--lime)"/>
        <line x1="186" y1="0" x2="186" y2="116" stroke="var(--grey-line)"/>
        <line x1="0" y1="72" x2="110" y2="72" stroke="var(--grey-line)"/>
        <line x1="0" y1="136" x2="80" y2="136" stroke="var(--olive)"/>
      </g>

      <!-- globe illustration area -->
      <ellipse role="img" aria-label="Network globe illustration of connected nodes" cx="378" cy="152" rx="128" ry="122" fill="url(#globeFill)"/>

      <!-- swoosh band -->
      <path class="swoosh" d="M0 278 C 220 320, 520 250, 640 50 L 630 80 C 520 260, 240 320, 0 298 Z" fill="url(#swooshFill)"/>

      <!-- decorative network area, right -->
      <rect role="img" aria-label="Decorative circuit and molecular network illustration" x="560" y="0" width="178" height="305" fill="url(#networkFill)"/>

      <!-- regulatory badges -->
      <g class="badges" fill="var(--white)">
        <rect x="14" y="234" width="28" height="33"/>
        <rect x="73" y="234" width="34" height="32"/>
        <rect x="139" y="236" width="44" height="28"/>
      </g>
    </svg>

    <div class="product-name">CORVANE +</div>
    <div class="brand-name">VANTERCELL</div>
    <div class="spec-text">110AH LiFEPO4<br>12.8V Battery</div>
  </section>
</div>
</body>
</html>
```